Maple Gable Business Card

Colors can be blue, grey and white as you see in the attached logo. Needs to have a spot for name, title, phone, email, address, and website. There also needs to be a spot for an agent's picture.

Contact Information for Business Card

See project description.

Colors

Designer to choose colors to be used in the design.

```html
<!DOCTYPE html>
<html lang="en">
<head>
<meta charset="utf-8">
<title>Maple Gable Business Card</title>
<link href="https://fonts.googleapis.com/css2?family=Roboto:wght@300;400;700&display=swap" rel="stylesheet">
<style>
  :root {
    --backdrop: #9b9b9b;
    --brand-blue: #2777b8;
    --slate: #58585b;
    --paper: #ffffff;
    --ink: #3b3b3d;
    --rule: #4a4a4a;
    --photo-top: #eef0f2;
    --photo-bottom: #1e2228;
  }
  * { box-sizing: border-box; margin: 0; padding: 0; }
  html, body { width: 1200px; height: 900px; overflow: hidden; }
  body {
    background: var(--backdrop);
    font-family: "Roboto", Arial, sans-serif;
    position: relative;
  }
  .card {
    position: absolute;
    top: 214px;
    width: 270px;
    height: 474px;
    border-radius: 24px;
    overflow: hidden;
  }
  .card-front { left: 288px; background: var(--brand-blue); }
  .card-back { left: 641px; background: var(--paper); text-align: center; color: var(--ink); }

  .front-band {
    position: absolute; left: 0; top: 0; width: 100%; height: 170px;
    background: var(--slate);
    border-bottom: 10px solid var(--paper);
  }
  .front-brand {
    position: absolute; left: 0; right: 0; top: 388px;
    display: flex; align-items: center; justify-content: center; gap: 10px;
    color: var(--paper);
    font-weight: 700; font-size: 22px; letter-spacing: 0.5px; text-transform: uppercase;
  }
  .front-brand .mark { width: 14px; height: 14px; background: var(--paper); }

  .agent-name { margin-top: 30px; color: var(--brand-blue); font-weight: 700; font-size: 20px; }
  .agent-title { margin-top: 2px; font-size: 14px; font-weight: 400; color: #222; }
  .contact-divider {
    margin: 8px auto 0; width: 156px; display: flex; align-items: center; gap: 2px;
  }
  .contact-divider .line { flex: 1; height: 1px; background: var(--rule); }
  .contact-divider svg { display: block; }
  .contact-list { margin-top: 8px; font-size: 13.5px; font-weight: 300; line-height: 17px; }
  .contact-list .accent { color: var(--brand-blue); }
  .section-rule { margin: 9px auto 0; width: 156px; height: 1px; background: var(--rule); }
  .address { margin-top: 10px; font-size: 13.5px; font-weight: 300; line-height: 17px; }
  .agent-photo {
    position: absolute; left: 0; right: 0; bottom: 0; height: 240px;
    background: linear-gradient(180deg, var(--photo-top) 0%, #d9dadc 40%, var(--photo-bottom) 100%);
  }
</style>
</head>
<body>
  <section class="card card-front">
    <div class="front-band"></div>
    <div class="front-brand"><span class="mark"></span>Maple Gable</div>
  </section>

  <section class="card card-back">
    <h1 class="agent-name">Daniel Harper</h1>
    <p class="agent-title">Manager</p>
    <div class="contact-divider">
      <span class="line"></span>
      <svg width="56" height="17" viewBox="0 0 56 17" aria-hidden="true">
        <g fill="#2777b8">
          <circle cx="8.5" cy="8.5" r="8"/>
          <circle cx="27.5" cy="8.5" r="8"/>
          <circle cx="46.5" cy="8.5" r="8"/>
        </g>
        <path d="M4.5 8 q4-3 8 0 v1.5 h-2 v-1 h-4 v1 h-2z M5.5 10.5 h6 v2 h-6z" fill="#fff"/>
        <rect x="22.5" y="5" width="10" height="7" fill="none" stroke="#fff" stroke-width="1.3"/>
        <path d="M22.5 5 l5 4 l5-4" fill="none" stroke="#fff" stroke-width="1.3"/>
        <g fill="none" stroke="#fff" stroke-width="1.2">
          <circle cx="46.5" cy="8.5" r="4.5"/>
          <ellipse cx="46.5" cy="8.5" rx="2" ry="4.5"/>
          <path d="M42 8.5 h9"/>
        </g>
      </svg>
      <span class="line"></span>
    </div>
    <div class="contact-list">
      <p>555-318-2740</p>
      <p>daniel@maplegable.com</p>
      <p>www.<span class="accent">maplegablehomes</span>.com</p>
    </div>
    <div class="section-rule"></div>
    <div class="address">
      <p>48 Alder Lane, Brookfield</p>
      <p>OH, 44403</p>
    </div>
    <div class="agent-photo" role="img" aria-label="Portrait photo of the agent in a dark suit and tie"></div>
  </section>
</body>
</html>
```